Business card for a Exhibition booth fabrication company

Hi. My company would like to change our corporate name card. We are an events and Exhibition stand builder company. We would like our corporate name card to resonate what we do. I need someone to create something unique that relates to the industry that I am in. The graphic designer should be creative to incorporate the elements of my industry and try to blend in well in the design of the card. Our aim is to ensure that we are unique and our card can look different from our competitors.
Updates

Target Market(s)

Marketing and events manager from all companies

Contact Information for Business Card

The business card should have the following details:
Name
Job Title
Email
Website

Colors

Designer to choose colors to be used in the design.

Requirements
Must have
• The card must be look something that is relevant to the service that I am providing. My website is: www.velmora-buildworks.com
• You can see my website to get more information on what service that I am doing
Nice to have
• On the back of my card, I would like to have a globe image with the incorporation of my company logo. This is to indicate that my services can be done in any part of the world.

```html
<!DOCTYPE html>
<html lang="en">
<head>
<meta charset="utf-8">
<title>Velmora Buildworks – Business Card</title>
<link rel="stylesheet" href="https://fonts.googleapis.com/css2?family=Arimo:wght@400;700&family=Open+Sans:wght@400&display=swap">
<style>
  :root {
    --backdrop-light: #dcdddf;
    --backdrop-dark: #9c9da0;
    --card-black: #000000;
    --accent-red: #e31e24;
    --text-grey: #8c8c8c;
    --divider-grey: #4a4a4a;
    --wordmark-grey: #7a7a7a;
    --map-grey: #3c3c3c;
    --map-grey-light: #4a4a4a;
    --white: #ffffff;
  }
  * { margin: 0; padding: 0; box-sizing: border-box; }
  html, body { width: 1200px; height: 1118px; overflow: hidden; }
  body {
    position: relative;
    background: linear-gradient(90deg, var(--backdrop-light) 0%, var(--backdrop-dark) 100%);
    font-family: "Open Sans", sans-serif;
  }
  .card {
    position: absolute;
    left: 220px;
    width: 743px;
    height: 424px;
    background: var(--card-black);
    border-radius: 40px;
    overflow: hidden;
  }
  .card--front { top: 87px; }
  .card--back { top: 574px; }

  .brand-mark {
    position: absolute;
    left: 177px;
    top: 162px;
    width: 60px;
    height: 60px;
    border-radius: 50%;
    background: var(--accent-red);
  }
  .brand-wordmark {
    position: absolute;
    left: 40px;
    top: 243px;
    width: 350px;
    text-align: center;
    font-family: "Arimo", sans-serif;
    font-weight: 700;
    font-size: 21px;
    letter-spacing: 3px;
    color: var(--wordmark-grey);
    white-space: nowrap;
  }

  .divider {
    position: absolute;
    left: 401px;
    top: 101px;
    width: 2px;
    height: 224px;
    background: var(--divider-grey);
  }
  .details { position: absolute; left: 418px; top: 92px; }
  .person-name {
    font-family: "Arimo", sans-serif;
    font-weight: 700;
    font-size: 26px;
    letter-spacing: 0.5px;
    color: var(--accent-red);
    line-height: 32px;
  }
  .person-title {
    font-family: "Arimo", sans-serif;
    font-size: 20px;
    letter-spacing: 1px;
    color: var(--text-grey);
    line-height: 30px;
  }
  .address {
    margin-top: 12px;
    font-size: 18px;
    line-height: 26px;
    color: var(--text-grey);
  }
  .contact-list { list-style: none; margin-top: 12px; }
  .contact-item {
    display: flex;
    align-items: center;
    height: 34px;
    font-size: 18px;
    color: var(--text-grey);
    white-space: nowrap;
  }
  .contact-icon { width: 20px; height: 20px; margin-right: 11px; flex: none; }

  .world-map {
    position: absolute;
    left: 0;
    top: 62px;
    width: 743px;
    height: 290px;
    background: radial-gradient(ellipse 62% 58% at 55% 48%, var(--map-grey-light) 0%, var(--map-grey) 45%, rgba(40,40,40,0.6) 75%, rgba(0,0,0,0) 100%);
  }
  .back-wordmark {
    position: absolute;
    left: 0;
    top: 196px;
    width: 743px;
    text-align: center;
    font-family: "Arimo", sans-serif;
    font-weight: 700;
    font-size: 40px;
    letter-spacing: 4px;
    color: #c8c8c8;
    white-space: nowrap;
  }
  .back-url {
    position: absolute;
    left: 0;
    top: 382px;
    width: 743px;
    text-align: center;
    font-size: 20px;
    letter-spacing: 4.5px;
    color: var(--white);
    white-space: nowrap;
  }
</style>
</head>
<body>
  <section class="card card--front">
    <span class="brand-mark"></span>
    <div class="brand-wordmark">VELMORA BUILDWORKS</div>
    <div class="divider"></div>
    <div class="details">
      <div class="person-name">DANIEL HARLOW</div>
      <div class="person-title">PRESIDENT</div>
      <div class="address">Street Name, City Name<br>Zipcode - 01234</div>
      <ul class="contact-list">
        <li class="contact-item">
          <svg class="contact-icon" viewBox="0 0 20 20"><path d="M4 2l4 3-2 3c1 2.5 3 4.5 5.5 5.5l2-2 3.5 3.5-2.5 2.5C9 17 3 11 1.5 4.5z" fill="var(--accent-red)"/></svg>
          012-345-6789
        </li>
        <li class="contact-item">
          <svg class="contact-icon" viewBox="0 0 20 20"><rect x="1" y="4" width="18" height="12" fill="var(--accent-red)"/><path d="M1 4l9 7 9-7M1 16l7-6M19 16l-7-6" stroke="#000" stroke-width="1.3" fill="none"/></svg>
          info@velmora-buildworks.com
        </li>
        <li class="contact-item">
          <svg class="contact-icon" viewBox="0 0 20 20" fill="none" stroke="var(--accent-red)" stroke-width="1.5"><circle cx="10" cy="10" r="8.5"/><ellipse cx="10" cy="10" rx="3.8" ry="8.5"/><path d="M1.5 10h17M3 5.5h14M3 14.5h14"/></svg>
          www.velmora-buildworks.com
        </li>
      </ul>
    </div>
  </section>

  <section class="card card--back">
    <div class="world-map" role="img" aria-label="Dark grey world map across the card, showing the company works worldwide"></div>
    <div class="back-wordmark">VELMORA BUILDWORKS</div>
    <div class="back-url">www.velmora-buildworks.com</div>
  </section>
</body>
</html>
```